Stationery Design + Business Cards

Stationary (letterhead as A4 210x297mm and Letter 8.5"x11", preferably both master page + 2nd pages)

Also need business cards, standard size 50x88mm, can be vertical or horizontal.

You can use a front/back design for the business cards, or front only.

Looking at the uploaded file (devank, you already have that), I want it to use the first logo on the list (4 colors).

Alternative, try the grayscale version (second file).

I need the following information on the business card (in no particular order, let me know what you come up with): 

Firstname Lastlame 
Title 

Mobile +1 555-204-7391 

VelaMorn, Inc. 
24851 Birchwood Ridge Passage 
Alderbrook, KS 46099 
Tel. +1 555-368-4172 
Fax +1 555-619-0834 

Web: www.velamorn.example 
Twitter: twitter/VelaMorn or @VelaMorn 
Facebook: facebook.com/VelaMorn 

For letterhead, just the company name, address + phone number & fax number 

If you think the phone/fax or something else should not be on the business cards, or something could be missing, let me know.

```html
<!DOCTYPE html>
<html lang="en">
<head>
<meta charset="utf-8">
<title>VelaMorn Business Cards</title>
<link rel="stylesheet" href="https://fonts.googleapis.com/css2?family=Source+Sans+3:wght@400;600;700&display=swap">
<style>
  :root {
    --stage: #000000;
    --paper: #ffffff;
    --band: #d1d2d4;
    --ink: #58585a;
    --brand-blue: #1c4f9f;
    --brand-dot: #ef7a22;
    --label: #ffffff;
    --rule: #8a8a8c;
  }
  * { margin: 0; padding: 0; box-sizing: border-box; }
  html, body {
    width: 1200px; height: 900px; overflow: hidden;
    background: var(--stage);
    font-family: "Source Sans 3", "Myriad Pro", Arial, sans-serif;
    color: var(--ink);
  }
  .board { position: relative; width: 1200px; height: 900px; }

  .variant-label {
    position: absolute; color: var(--label);
    font-weight: 700; font-size: 21px; line-height: 26px;
    text-align: center; white-space: nowrap; transform: translateX(-50%);
  }

  .card { position: absolute; background: var(--band); overflow: hidden; }
  .card-top { position: absolute; left: 0; top: 0; width: 100%; background: var(--paper); }

  .brand { position: absolute; display: flex; align-items: center; }
  .brand-dot { border-radius: 50%; background: var(--brand-dot); flex: none; }
  .brand-name {
    color: var(--brand-blue); font-weight: 400; font-size: 48px;
    line-height: 50px; letter-spacing: -0.3px; margin-left: 8px;
  }

  .line { position: absolute; white-space: nowrap; }
  .centered { left: 0; width: 100%; text-align: center; }
  .person-name { font-weight: 700; font-size: 21px; line-height: 24px; }
  .person-title { font-weight: 400; font-size: 15.5px; line-height: 19px; }
  .person-mobile { font-weight: 700; font-size: 15.5px; line-height: 19px; }

  .block { position: absolute; font-weight: 600; white-space: nowrap; }
  .block p { display: block; }
  .small { font-size: 13px; line-height: 15.5px; }
  .medium { font-size: 15.5px; line-height: 19.5px; }
  .mid-small { font-size: 13.5px; line-height: 17px; }
  .align-right { text-align: right; }
  .align-center { text-align: center; left: 0; width: 100%; }
  .divider { position: absolute; width: 1px; background: var(--rule); }
</style>
</head>
<body>
<main class="board">

  <div class="variant-label" style="left:367px; top:95px;">Horizontal B. card Front Only</div>
  <section class="card card-horizontal-split" style="left:80px; top:127px; width:581px; height:330px;">
    <div class="card-top" style="height:108px;"></div>
    <div class="brand" style="left:306px; top:51px;">
      <span class="brand-dot" style="width:36px; height:36px;"></span>
      <span class="brand-name">VelaMorn</span>
    </div>
    <p class="line centered person-name" style="top:154px;">Firstname Lastname</p>
    <p class="line centered person-title" style="top:177px;">Title</p>
    <p class="line centered person-mobile" style="top:196px;">Mobile +1 555-204-7391</p>

    <div class="block small align-right" style="right:307px; top:261px;">
      <p>Web: www.velamorn.example</p>
      <p>Twitter: twitter/VelaMorn or @VelaMorn</p>
      <p>Facebook: facebook.com/VelaMorn</p>
    </div>
    <span class="divider" style="left:290px; top:254px; height:60px;"></span>
    <div class="block small" style="left:306px; top:253px;">
      <p>VelaMorn, Inc.</p>
      <p>24851 Birchwood Ridge Passage</p>
      <p>Alderbrook, KS 46099</p>
      <p>Tel. +1 555-368-4172, Fax +1 555-619-0834</p>
    </div>
  </section>

  <div class="variant-label" style="left:373px; top:481px;">Horizontal B. card Front Only</div>
  <section class="card card-horizontal-stacked" style="left:86px; top:508px; width:581px; height:330px;">
    <div class="card-top" style="height:108px;"></div>
    <div class="brand" style="left:306px; top:49px;">
      <span class="brand-dot" style="width:36px; height:36px;"></span>
      <span class="brand-name">VelaMorn</span>
    </div>
    <p class="line centered person-name" style="top:141px;">Firstname Lastname</p>
    <p class="line centered person-title" style="top:164px;">Title</p>
    <p class="line centered person-mobile" style="top:183px;">Mobile +1 555-204-7391</p>

    <div class="block small align-center" style="top:232px;">
      <p>VelaMorn, Inc.</p>
      <p>24851 Birchwood Ridge Passage, Alderbrook, KS 46099</p>
      <p>Tel. +1 555-368-4172, Fax +1 555-619-0834</p>
    </div>
    <div class="block small align-center" style="top:287px;">
      <p>Web: www.velamorn.example</p>
      <p>Twitter: twitter/VelaMorn or @VelaMorn&nbsp;&nbsp;Facebook: facebook.com/VelaMorn</p>
    </div>
  </section>

  <div class="variant-label" style="left:963px; top:174px;">Vertical B. card Front Only</div>
  <section class="card card-vertical" style="left:790px; top:211px; width:330px; height:582px;">
    <div class="card-top" style="height:223px;"></div>
    <div class="brand" style="left:60px; top:154px;">
      <span class="brand-dot" style="width:38px; height:38px;"></span>
      <span class="brand-name">VelaMorn</span>
    </div>
    <p class="line centered person-name" style="top:280px;">Firstname Lastname</p>
    <p class="line centered person-title" style="top:303px;">Title</p>
    <p class="line centered person-mobile" style="top:322px;">Mobile +1 555-204-7391</p>

    <div class="block medium align-center" style="top:394px;">
      <p>VelaMorn, Inc.</p>
      <p>24851 Birchwood Ridge Passage</p>
      <p>Alderbrook, KS 46099</p>
      <p>Tel. +1 555-368-4172</p>
      <p>Fax +1 555-619-0834</p>
    </div>
    <div class="block mid-small align-center" style="top:512px;">
      <p>Web: www.velamorn.example</p>
      <p>Twitter: twitter/VelaMorn or @VelaMorn</p>
      <p>Facebook: facebook.com/VelaMorn</p>
    </div>
  </section>

</main>
</body>
</html>
```